4th Generation Family Business Needs a New Card Design!

We are a family owned 4th Generation company. We are based in the Sydney, Australia area and we are desperately in need of a more modern and classy card. We are monumental masons who design, supply & erect lasting memorials throughout cemeteries in Sydney. Our customers are normally in a period of grieving. I have attached logo files that will need to be implemented on the card. Company was established 1935. Australian Owned and Operated. Card needs to be designed to PIXO.com specification.

Target Market(s)

Our target market is based upon people that a grieving for family members that have passed away. We also deal with alot of companies that own and operate cemeteries.

Industry/Entity Type

Business

Contact Information for Business Card

Simon Harcourt, Operations Manager, 0417293086, simon@harcourtmemorials.com.au
Lewis Harcourt, Director, 0491630572, lewis@harcourtmemorials.com.au
Phone # 02 9561 3048
Website: www.harcourtmemorials.com.au
Address: Suite 17, 8 Palfrey Lane, West Carlow, Sydney NSW 2156

Font styles to use
Serif
Decorative
Script

Requirements
Must have
• Would like to see the logo nicely implemented with a modern design. Embossed lettering would be a nice additive.

```html
<!DOCTYPE html>
<html lang="en">
<head>
<meta charset="utf-8">
<title>Harcourt Memorials – Business Card</title>
<link rel="stylesheet" href="https://fonts.googleapis.com/css2?family=Cinzel:wght@500&family=Open+Sans:wght@400&display=swap">
<style>
  :root {
    --bg: #e4e4e4;
    --card: #ffffff;
    --ink: #1f1d1e;
    --charcoal: #2b292a;
    --gold: #f0c22e;
    --light: #f2f2f2;
  }
  * { box-sizing: border-box; margin: 0; padding: 0; }
  html, body { width: 1200px; height: 950px; overflow: hidden; }
  body {
    background: var(--bg);
    position: relative;
    font-family: "Open Sans", Arial, sans-serif;
  }
  .card {
    position: absolute;
    left: 250px;
    width: 700px;
    height: 400px;
    background: var(--card);
    box-shadow: 0 6px 18px rgba(0,0,0,.18);
    overflow: hidden;
  }
  .card--front { top: 50px; }
  .card--back { top: 500px; }

  /* Wordmark */
  .brand {
    position: absolute;
    display: flex;
    align-items: center;
    gap: 14px;
    font-family: "Cinzel", Georgia, serif;
    font-weight: 500;
    color: var(--ink);
    letter-spacing: 1px;
    white-space: nowrap;
  }
  .brand__square { width: 30px; height: 30px; background: var(--gold); flex: none; }
  .brand__name { line-height: 1.2; text-align: center; }

  .card--front .brand {
    left: 50%; top: 50%;
    transform: translate(-50%, -50%);
    font-size: 38px;
  }

  /* Back */
  .back-art { position: absolute; inset: 0; }
  .card--back .brand {
    left: 40px; top: 150px;
    font-size: 24px;
  }
  .card--back .brand__square { width: 20px; height: 20px; }
  .person {
    position: absolute;
    right: 150px; top: 46px;
    text-align: right;
    font-family: "Cinzel", Georgia, serif;
    font-weight: 500;
    white-space: nowrap;
  }
  .person__name { font-size: 24px; color: var(--ink); letter-spacing: 1px; }
  .person__role { font-size: 15px; color: var(--gold); letter-spacing: 1px; margin-top: 2px; }
  .monogram-panel {
    position: absolute;
    left: 478px; top: 110px;
    width: 176px; height: 176px;
    background: var(--card);
    border: 4px solid var(--ink);
    display: flex; align-items: center; justify-content: center;
    font-family: "Cinzel", Georgia, serif;
    font-weight: 500;
    font-size: 24px;
    color: var(--ink);
  }
  .address {
    position: absolute;
    left: 40px; top: 232px;
    color: var(--light);
    font-size: 14px;
    line-height: 21px;
    white-space: nowrap;
  }
  .contacts {
    position: absolute;
    left: 40px; top: 282px;
    list-style: none;
    color: var(--light);
    font-size: 14px;
    line-height: 19px;
    white-space: nowrap;
  }
  .contacts li { display: flex; align-items: center; gap: 9px; }
  .contacts svg { width: 12px; height: 12px; flex: none; fill: var(--gold); }
</style>
</head>
<body>

<section class="card card--front" aria-label="Card front">
  <div class="brand"><span class="brand__square"></span><span class="brand__name">Harcourt<br>Memorials</span></div>
</section>

<section class="card card--back" aria-label="Card back">
  <svg class="back-art" viewBox="0 0 700 400" aria-hidden="true">
    <rect x="565" y="75" width="135" height="290" fill="var(--gold)"/>
    <polygon points="0,210 470,210 560,145 565,145 565,365 0,365" fill="var(--charcoal)"/>
    <rect x="565" y="300" width="135" height="65" fill="var(--charcoal)"/>
  </svg>

  <div class="person">
    <div class="person__name">Simon Harcourt</div>
    <div class="person__role">Operations Manager</div>
  </div>

  <div class="brand"><span class="brand__square"></span><span class="brand__name">Harcourt Memorials</span></div>

  <div class="monogram-panel">Harcourt</div>

  <p class="address">Suite 17, 8 Palfrey Lane<br>West Carlow, Sydney NSW 2156</p>

  <ul class="contacts">
    <li><svg viewBox="0 0 12 12"><path d="M2 1l2 0 1 3-1.5 1a7 7 0 0 0 3.5 3.5L8 7l3 1v2a1 1 0 0 1-1 1A9 9 0 0 1 1 2a1 1 0 0 1 1-1z"/></svg>02 9561 3048</li>
    <li><svg viewBox="0 0 12 12"><path d="M3 0h6a1 1 0 0 1 1 1v10a1 1 0 0 1-1 1H3a1 1 0 0 1-1-1V1a1 1 0 0 1 1-1zm0 2v7h6V2z"/></svg>0417293086</li>
    <li><svg viewBox="0 0 12 12"><path d="M0 2h12v8H0zm1 1v.4l5 3.2 5-3.2V3z"/></svg>simon@harcourtmemorials.com.au</li>
    <li><svg viewBox="0 0 12 12"><circle cx="6" cy="6" r="6"/></svg>www.harcourtmemorials.com.au</li>
  </ul>
</section>

</body>
</html>
```